Events Company Needs Website Revamp

Tallwood Expos is an events company that specializes in organizing and marketing large scale consumer and trade events globally.

The new web design should provide easy classification of the events, and allow visitors to find and access the details page within 2 clicks.

There are no strict guidelines on the color theme. It just has to blend naturally with the corporate logo.
Updates

The company logo is uploaded (pdf & ai)

I came across this design which I like very much. Elegant and corporate with nice modern fonttype.

Layout wise, neat and clear. 

Please see how you can emulate the design further. Particularly, highlighting the 2 event arms (Trade/Consumer) clearly.

Target Market(s)

Consumer looking for upcoming events, B2C companies looking to participate, B2B companies looking to connect with other companies

Industry/Entity Type

It Company

Requirements
Must have
• The new design should help to achieve the following objectives:
1) Visitors should be able to easily identify and access the 2 different types of events (i.e. Trade Events and Consumer Events).
2) Visitors should be able to easily find events that interest them (e.g. filter by date, trade or consumer, category [i.e. beauty, retail, F&B, construction, etc.]).
3) Visitors should be able to access an event’s details page within 2 clicks from any page.

Main navigation to include the following links:
- About Us
- Calendar
- Consumer Events
- Trade Events
- Contact Us

Design for Three (3) pages required:
A. Homepage
- Clear differentiation and easy access to the 2 different types of events (trade and consumer)
- Featured area to showcase latest 4-5 events
- Quick way to access events calendar
- Clear call-to-action for newsletter signup
- Social media sharing widgets/buttons
- A section for latest news and press releases
- A section for featured testimonials

B. Events Listing Page
- List of links to all events
- Logos and/or photos of events
- Filter / tags to find events in a specific category (e.g. food, electronics, building & construction, etc.)

C. Events Details Page
- Photo strip to showcase event photos / brochure
- A section with event details (Date, Venue, Event Description, etc.)
- Call-to-action button to visit event website
- Call-to-action button to contact event sales team
- E.g. http://vantly-demo.com/user/brightfoxhk/brightfox-monday-2011 but with the photo strip permanently extended and of a shorter height. Event details and call-to-action buttons should also be easily seen

```html
<!DOCTYPE html>
<html lang="en">
<head>
<meta charset="utf-8">
<title>Tallwood Expos</title>
<link href="https://fonts.googleapis.com/css2?family=Questrial&family=Open+Sans:wght@400;600&family=Cedarville+Cursive&display=swap" rel="stylesheet">
<style>
:root{
  --red:#e8173f;
  --blue:#1a5aa0;
  --orange:#f7a400;
  --peach:#f4c08c;
  --card:#f1f1f1;
  --tab:#e6e6e6;
  --line:#dcdcdc;
  --text:#222;
  --muted:#8a9ab5;
}
*{box-sizing:border-box;margin:0;padding:0}
html,body{width:1029px;height:1200px;overflow:hidden;background:#fff}
body{position:relative;font-family:"Open Sans",Arial,sans-serif;color:var(--text)}
.abs{position:absolute}
.frame{left:60px;top:0;width:909px;height:1200px;border-left:1px solid #eee;border-right:1px solid #eee}
.brand{left:78px;top:28px;width:130px}
.brand-name{display:flex;align-items:center;gap:6px;font-family:"Questrial",sans-serif;font-size:19px;color:var(--red)}
.brand-dot{width:14px;height:14px;border-radius:50%;background:var(--orange)}
.brand-sub{margin-top:34px;font-size:7px;color:var(--blue);letter-spacing:.2px}
.nav{font-family:"Questrial",sans-serif;font-size:11.5px;color:#333;text-transform:uppercase}
.nav-item{position:absolute;top:46px;text-align:center;padding-bottom:8px;border-bottom:1px solid var(--line)}
.sub{position:absolute;top:76px;list-style:none;font-size:8.5px;line-height:16px;color:#333}
.sub li::before{content:"";display:inline-block;width:5px;height:5px;background:var(--red);margin-right:5px;vertical-align:1px}
.tel{position:absolute;left:870px;top:72px;font-size:8.5px;line-height:16px;color:var(--red);font-weight:600}
.hero{left:68px;top:143px;width:893px;height:310px;background:linear-gradient(180deg,#5d6a7a 0%,#a99a70 30%,#e6b63c 55%,#3b3a33 78%,#27303a 100%)}
.ribbon{position:absolute;top:0;background:var(--red);border-radius:0 0 30px 30px;color:#fff}
.ribbon span{position:absolute;left:50%;bottom:40px;transform:translateX(-50%) rotate(-90deg);transform-origin:center;white-space:nowrap;font-family:"Questrial",sans-serif}
.ribbon i{position:absolute;left:50%;bottom:14px;width:12px;height:12px;margin-left:-6px;border-radius:50%;background:#fff}
.hero-caption{position:absolute;left:134px;top:234px;width:740px;font-family:"Questrial",sans-serif;font-size:21px;line-height:26px;color:#fff}
.h2{font-family:"Questrial",sans-serif;font-size:21px;color:var(--blue)}
.tabs{left:657px;top:463px;height:33px;display:flex;align-items:center;font-family:"Questrial",sans-serif;font-size:15px}
.tab-on{background:var(--tab);color:var(--red);padding:8px 11px 0;height:33px}
.rule{height:1px;background:var(--line)}
.card{width:423px;height:121px;background:var(--card);border-radius:8px}
.thumb{position:absolute;left:8px;top:10px;width:98px;height:98px;border:3px solid var(--peach);background:#fff}
.thumb div{width:100%;height:100%}
.card-body{position:absolute;left:123px;top:13px;width:290px;font-size:8.8px;line-height:13px}
.date{color:#1a8ad0}
.btn{position:absolute;display:inline-block;font-size:9px;border-radius:10px;text-align:center;line-height:18px}
.btn-red{background:var(--red);color:#fff;width:64px;height:18px;box-shadow:0 1px 2px #999}
.btn-light{background:#fff;color:var(--red);border:1px solid #ccc;width:62px;height:20px}
.sec-tab{background:var(--tab);padding:4px 12px 0;height:32px}
.news{width:200px;font-size:8.8px;line-height:16px}
.news .nthumb{position:absolute;width:64px;height:60px;border:1px solid #ddd;background:#fff}
.news .nthumb div{position:absolute;inset:4px}
.news .ntitle{position:absolute;left:74px;width:126px}
.news .date2{color:var(--red)}
.news p{position:absolute;top:70px;text-align:justify}
.press{left:523px;top:822px;width:422px;height:221px;border:1px solid #ccc}
.press p{position:absolute;left:96px;width:314px;font-size:8.8px;line-height:16px;text-align:justify}
.press .pthumb{position:absolute;left:14px;width:68px;height:64px;border:3px solid #e2e2e2;background:#fff}
.press .pthumb div{position:absolute;inset:4px}
.testi{left:68px;top:1053px;width:893px;height:73px;background:var(--red);border-radius:8px;color:#fff;box-shadow:0 2px 3px #bbb}
.testi h3{position:absolute;left:12px;top:14px;font-weight:400;font-size:12px;font-family:"Questrial",sans-serif}
.testi q{position:absolute;left:94px;top:35px;font-size:9.5px}
.slider{position:absolute;left:657px;top:11px;width:223px;height:4px;background:#c0102f;border-radius:2px}
.slider i{position:absolute;left:90px;top:0;width:44px;height:4px;background:#fff;border-radius:2px}
.foot{font-size:8px;line-height:15px;color:var(--muted)}
.connect{left:753px;top:1144px;font-family:"Cedarville Cursive",cursive;font-size:14px;color:#444}
.social{left:858px;top:1146px;display:flex;gap:5px}
.social span{width:15px;height:15px;background:#9aa7bb;border-radius:2px}
.side{left:969px;width:33px;color:#fff;font-family:"Questrial",sans-serif;font-size:15px}
.side span{position:absolute;left:50%;top:50%;transform:translate(-50%,-50%) rotate(90deg);white-space:nowrap}
</style>
</head>
<body>
<div class="abs frame"></div>

<header>
  <div class="abs brand">
    <div class="brand-name"><span class="brand-dot"></span>Tallwood Expos</div>
    <div class="brand-sub">A SUBSIDIARY OF NORVANE MEDIA</div>
  </div>
  <nav class="nav">
    <div class="nav-item" style="left:242px;width:68px">Home</div>
    <div class="nav-item" style="left:326px;width:102px">About Us</div>
    <div class="nav-item" style="left:444px;width:98px">Calendar</div>
    <div class="nav-item" style="left:558px;width:158px">Consumer Events</div>
    <div class="nav-item" style="left:732px;width:124px">Trade Events</div>
    <div class="nav-item" style="left:872px;width:96px">Contact</div>
  </nav>
  <ul class="sub" style="left:336px"><li>Media Releases</li><li>Associated Companies</li><li>Gallery</li></ul>
  <ul class="sub" style="left:586px"><li>Media Releases</li><li>Associated Companies</li><li>Gallery</li></ul>
  <ul class="sub" style="left:756px"><li>Media Releases</li><li>Associated Companies</li><li>Gallery</li></ul>
  <div class="tel">Tel: (65) 6100-2040<br><span style="padding-left:16px">(65) 6100-2041</span></div>
</header>

<section class="abs hero" role="img" aria-label="City skyline with observation wheel at sunset over the water">
  <div class="ribbon" style="left:40px;width:57px;height:225px"><span style="font-size:24px;bottom:100px">innovative</span><i></i></div>
  <div class="ribbon" style="left:114px;width:58px;height:140px;opacity:.85"><span style="font-size:15px;bottom:70px;opacity:.7">entertain</span><i></i></div>
  <div class="ribbon" style="left:189px;width:59px;height:140px;opacity:.85"><span style="font-size:15px;bottom:70px;opacity:.7">value-ad</span><i></i></div>
  <p class="hero-caption">Conceptualize events that are strongly themed and create synergy with business partners offerings.</p>
</section>

<section>
  <h2 class="abs h2" style="left:80px;top:467px">Featured Events</h2>
  <div class="abs tabs"><span class="tab-on">consumer events</span><span style="color:var(--blue);margin:0 14px 0 4px">|</span><span style="color:var(--blue)">trade events</span></div>
  <div class="abs rule" style="left:68px;top:496px;width:893px"></div>

  <article class="abs card" style="left:82px;top:506px">
    <div class="thumb"><div role="img" aria-label="Parenting fair event logo" style="background:linear-gradient(135deg,#f7b84a,#e95b8c,#4aa3df)"></div></div>
    <div class="card-body">Lorem ipsum dolor sit amet consec tetu eripsum dolor<br><span class="date">January 24, 2011 · 8 Comments</span><br>Lorem ipsum dolor sit amet, consec tetuer adipiscing elit. Praesent vestibulum molestie lacus. Aenean nonummyhendrerit mauris. Phasellus porta.</div>
    <a class="btn btn-red" style="left:323px;top:87px">Read More</a>
  </article>
  <article class="abs card" style="left:522px;top:506px">
    <div class="thumb"><div role="img" aria-label="Food and electronics fair event logo" style="background:radial-gradient(circle,#c8102e 40%,#fff 75%)"></div></div>
    <div class="card-body">Lorem ipsum dolor sit amet consec tetu eripsum dolor<br><span class="date">January 24, 2011 · 8 Comments</span><br>Lorem ipsum dolor sit amet, consec tetuer adipiscing elit. Praesent vestibulum molestie lacus. Aenean nonummyhendrerit mauris. Phasellus porta.</div>
    <a class="btn btn-red" style="left:323px;top:87px">Read More</a>
  </article>
  <article class="abs card" style="left:82px;top:641px">
    <div class="thumb"><div role="img" aria-label="Children's learning fair event logo" style="background:linear-gradient(135deg,#fbd34a,#f28c28,#8cc63f)"></div></div>
    <div class="card-body">Lorem ipsum dolor sit amet consec tetu eripsum dolor<br><span class="date">January 24, 2011 · 8 Comments</span><br>Lorem ipsum dolor sit amet, consec tetuer adipiscing elit. Praesent vestibulum molestie lacus. Aenean nonummyhendrerit mauris. Phasellus porta.</div>
    <a class="btn btn-red" style="left:323px;top:87px">Read More</a>
  </article>
  <article class="abs card" style="left:522px;top:641px">
    <div class="thumb"><div role="img" aria-label="Culinary masters event logo" style="background:linear-gradient(180deg,#fff,#e9eef3)"></div></div>
    <div class="card-body">Lorem ipsum dolor sit amet consec tetu eripsum dolor<br><span class="date">January 24, 2011 · 8 Comments</span><br>Lorem ipsum dolor sit amet, consec tetuer adipiscing elit. Praesent vestibulum molestie lacus. Aenean nonummyhendrerit mauris. Phasellus porta.</div>
    <a class="btn btn-red" style="left:323px;top:87px">Read More</a>
  </article>
</section>

<section>
  <h2 class="abs h2 sec-tab" style="left:67px;top:786px">Latest News</h2>
  <div class="abs rule" style="left:68px;top:818px;width:437px"></div>

  <article class="abs news" style="left:76px;top:834px;height:190px">
    <div class="nthumb"><div role="img" aria-label="Food and electronics fair logo" style="background:linear-gradient(135deg,#fff,#f3d6d6)"></div></div>
    <div class="ntitle">Lorem ipsum dolor sit amet<br><span class="date2">January 24, 2011 · 8 Comments</span></div>
    <p style="width:194px">Lorem ipsum dolor sit amet, consec tetuer adipiscing elit. Praesent vestibulum molestie lacus. Aenean nonummyhendrerit mauris. Phasellus porta. Fusce suscipit varius mi. Cum sociis natoque penatibus et magnis dis parturient montes, nascetur ridiculus</p>
    <a class="btn btn-light" style="left:119px;top:173px">Read More</a>
  </article>
  <article class="abs news" style="left:291px;top:834px;height:190px">
    <div class="nthumb"><div role="img" aria-label="Food tour event logo" style="background:linear-gradient(135deg,#fff,#f6e3c8)"></div></div>
    <div class="ntitle">Lorem ipsum dolor sit amet<br><span class="date2">January 24, 2011 · 8 Comments</span></div>
    <p style="width:194px">Lorem ipsum dolor sit amet, consec tetuer adipiscing elit. Praesent vestibulum molestie lacus. Aenean nonummyhendrerit mauris. Phasellus porta. Fusce suscipit varius mi. Cum sociis natoque penatibus et magnis dis parturient montes, nascetur ridiculus</p>
    <a class="btn btn-light" style="left:128px;top:173px">Read More</a>
  </article>

  <h2 class="abs h2 sec-tab" style="left:522px;top:786px;width:159px">Press Release</h2>
  <div class="abs rule" style="left:522px;top:818px;width:439px"></div>
  <div class="abs press">
    <div class="pthumb" style="top:20px"><div role="img" aria-label="Gifts and electronics fair logo" style="background:linear-gradient(135deg,#fff,#f4d3d3,#d7ead0)"></div></div>
    <p style="top:18px">Lorem ipsum dolor sit amet, consec tetuer adipiscing elit. Praesent vestibulum molestie lacus. Aenean nonummyhendrerit mauris. Phasellus porta. Fusce suscipit varius mi. Cum sociis natoque penatibus et magnis dis parturient montes, nascetur ridiculus</p>
    <a class="btn btn-light" style="left:334px;top:85px">Read More</a>
    <div class="pthumb" style="top:113px"><div role="img" aria-label="Food and electronics fair logo" style="background:linear-gradient(135deg,#fff,#f3d6d6)"></div></div>
    <p style="top:113px">Lorem ipsum dolor sit amet, consec tetuer adipiscing elit. Praesent vestibulum molestie lacus. Aenean nonummyhendrerit mauris. Phasellus porta. Fusce suscipit varius mi. Cum sociis natoque penatibus et magnis dis parturient montes, nascetur ridiculus</p>
    <a class="btn btn-light" style="left:334px;top:193px">Read More</a>
  </div>
</section>

<section class="abs testi">
  <h3>Testimonials
    <svg width="28" height="18" viewBox="0 0 28 18" style="vertical-align:-5px"><path d="M6 15c-4 0-5-5-2-6-1-4 4-6 6-3 2-4 9-3 9 1 4-1 7 3 4 6 1 2-1 3-3 3z" fill="#fff"/></svg>
  </h3>
  <q>Aenean nonummy hendrerit mauris. Phasellus porta. Fusce suscipit varius mi. Cum sociis natoque suscipit varius.</q><span class="abs" style="left:678px;top:35px;font-size:9.5px">- Marla</span>
  <div class="slider"><i></i></div>
</section>

<footer>
  <div class="abs foot" style="left:76px;top:1144px">Copyright © Tallwood Expos 2008-2010. All Rights Reserved.<br>Tel: (65) 6100-2040 or (65) 6100-2041 &nbsp;•&nbsp; Fax: (65) 6100-2140 &nbsp;•&nbsp; hello@tallwoodexpos.example</div>
  <div class="abs connect">connect with us</div>
  <div class="abs social" aria-label="Social media links"><span></span><span></span><span></span><span></span><span></span></div>
</footer>

<a class="abs side" style="top:520px;height:219px;background:var(--blue)"><span>view our calendar</span></a>
<a class="abs side" style="top:797px;height:219px;background:var(--orange)"><span>newsletter sign up</span></a>
</body>
</html>
```